Brevlon Website Design - Wordpress

Need a website WordPress design for our existing website that we just stood up. The logo is already in place and name. Brevlon.example We are a company which makes connections with our clients through educating them and providing networking events. We would like for the website to show a VIP/special feel to it.

Target Market(s)

Business executives and employees. Age group 26-65 in the following sectors:
- Technology
- Human Resources
- Finance
- Sales

Industry/Entity Type

Technical Service

Number of Pages Required

4 page

Font styles to use
Sans Serif

Requirements
Must have
• Must be something for Wordpress
Nice to have
• Would like this to be professional but look cutting edge and VIP.

```html
<!DOCTYPE html>
<html lang="en">
<head>
<meta charset="utf-8">
<title>Brevlon — Connect, Educate, Expand</title>
<link href="https://fonts.googleapis.com/css2?family=Quicksand:wght@300;400;500;600;700&family=Open+Sans:wght@400;600&display=swap" rel="stylesheet">
<style>
:root{
  --ink:#1c1c1c;
  --text:#444;
  --muted:#6b6b6b;
  --blue:#1f4e8c;
  --red:#c8202f;
  --purple:#6b2c8a;
  --yellow:#e3a21a;
  --gold:#d9a21b;
  --dark:#111;
  --soft:#f2f2f2;
  --line:#3a3a3a;
}
*{margin:0;padding:0;box-sizing:border-box}
html,body{width:1200px;height:3766px;overflow:hidden}
body{position:relative;font-family:"Quicksand",sans-serif;color:var(--ink);background:#fff}
.abs{position:absolute}
.center{text-align:center;left:0;width:1200px}
p.small{font-family:"Open Sans",sans-serif;font-size:12px;line-height:22px;color:var(--muted)}

/* hero */
.brand{font-weight:500;letter-spacing:6px;color:#fff;font-size:34px}
.nav{position:absolute;top:52px;right:110px;display:flex;gap:50px;font-size:14px;font-weight:600;color:#fff}
.nav .active{color:var(--gold)}
.hero-title{top:255px;font-size:104px;font-weight:400;color:#fff;letter-spacing:2px}
.hero-sub{top:390px;font-size:21px;line-height:42px;color:#fff;font-weight:500}
.btn{display:inline-block;border-radius:30px;font-weight:600;color:#fff}
.hero-btn{left:519px;top:490px;width:163px;height:50px;line-height:50px;background:var(--red);font-size:18px;text-align:center}

/* strategy */
.sec-title{font-size:30px;font-weight:500}
.sec-sub{font-size:14px;color:var(--text)}
.trait{width:250px}
.trait h3{font-size:28px;font-weight:600}
.trait h3 small{font-size:13px;font-weight:500;color:var(--muted)}
.trait p{margin-top:12px}
.t-right{text-align:right}

/* about */
.about{position:absolute;left:0;top:1375px;width:1200px;height:671px;background:linear-gradient(90deg,#f7f7f7,#ececec)}
.person{position:absolute;width:440px;text-align:center}
.portrait{width:152px;height:152px;border-radius:50%;margin:0 auto;border:4px solid #fff;box-shadow:0 0 0 2px #cfd6e0}
.person h4{margin-top:36px;font-size:16px;line-height:28px;font-weight:500;color:var(--ink)}
.person p{margin-top:14px}
.outline-btn{display:inline-block;margin-top:18px;width:135px;height:45px;line-height:43px;border:2px solid var(--blue);color:var(--blue);font-weight:600;font-size:16px;background:#fff;border-radius:3px}

/* expand */
.expand{position:absolute;left:0;top:2046px;width:1200px;height:520px;background:linear-gradient(100deg,#c0392b 0%,#b3203a 45%,#6b2c8a 100%)}
.expand-title{top:2130px;font-size:64px;font-weight:500;color:#fff}
.expand-body{left:110px;top:2236px;width:980px;text-align:center;font-size:14px;line-height:31px;color:#fff;font-weight:500}
.expand-btn{left:478px;top:2425px;width:245px;height:60px;line-height:60px;text-align:center;background:var(--yellow);font-size:17px}

/* events */
.card{position:absolute;top:2729px;width:314px;height:429px;border:1px solid #ddd;background:#fff;text-align:center}
.card .pic{height:226px}
.card h5{margin-top:14px;font-size:16px;font-weight:500;padding-top:12px}
.card .date{margin-top:12px;font-size:13px;color:var(--red);font-weight:600}
.card p.small{margin:10px 20px 0;font-size:11px}

/* footer */
.foot-col{position:absolute;top:3472px;width:320px;text-align:center;color:#fff}
.foot-icon{width:70px;height:70px;border-radius:50%;border:2px solid #fff;margin:0 auto;display:flex;align-items:center;justify-content:center}
.foot-col h6{margin-top:20px;font-size:22px;font-weight:500}
.foot-col p{margin-top:10px;font-size:12px;line-height:23px;color:#ddd;font-family:"Open Sans",sans-serif}
.copy{top:3710px;font-size:13px;color:#fff;font-family:"Open Sans",sans-serif}
</style>
</head>
<body>

<!-- hero -->
<svg class="abs" style="left:0;top:0" width="1200" height="740" viewBox="0 0 1200 740">
  <defs>
    <linearGradient id="heroShade" x1="0" y1="0" x2="1" y2="1">
      <stop offset="0" stop-color="#2b2b2b"/>
      <stop offset=".5" stop-color="#4a4a4a"/>
      <stop offset="1" stop-color="#1c1c1c"/>
    </linearGradient>
  </defs>
  <polygon points="0,0 1200,0 1200,600 600,728 0,600" fill="var(--red)"/>
  <polygon points="0,0 1200,0 1200,588 600,712 0,588" fill="url(#heroShade)" role="img" aria-label="Black and white photo of a coffee cup on a desk with a city skyline behind"/>
</svg>
<div class="brand abs" style="left:150px;top:40px">BREVLON</div>
<nav class="nav"><span class="active">HOME</span><span>EVENTS</span><span>EXPAND</span><span>X</span><span>ABOUT</span><span>CONNECT</span></nav>
<h1 class="abs center hero-title">BREVLON</h1>
<p class="abs center hero-sub">BREVLON provides impactful connection opportunities to help educate,<br>equip &amp; expand you and your business</p>
<span class="abs btn hero-btn">Read More</span>

<!-- strategy -->
<h2 class="abs center sec-title" style="top:766px">It's about our unique X Strategy</h2>
<p class="abs center sec-sub" style="top:826px">BREVLON provides impactful connection opportunities to help educate, equip &amp; expand you &amp; your business</p>

<svg class="abs" style="left:380px;top:885px" width="440" height="440" viewBox="0 0 440 440">
  <circle cx="220" cy="220" r="196" fill="#fff" stroke="#eee" stroke-width="2"/>
  <circle cx="220" cy="220" r="130" fill="#fff" stroke="#e6e6e6" stroke-width="10"/>
  <text x="220" y="230" text-anchor="middle" font-family="Quicksand, sans-serif" font-size="26" font-weight="500" letter-spacing="5" fill="#444">BREVLON</text>
  <g fill="#fff" stroke-width="3">
    <circle cx="59" cy="107" r="43" stroke="var(--blue)"/>
    <circle cx="385" cy="107" r="43" stroke="var(--red)"/>
    <circle cx="59" cy="340" r="43" stroke="var(--purple)"/>
    <circle cx="385" cy="340" r="43" stroke="var(--yellow)"/>
  </g>
  <g fill="none" stroke-width="2.5" stroke-linecap="round">
    <circle cx="59" cy="107" r="14" stroke="var(--blue)"/>
    <circle cx="59" cy="107" r="5" stroke="var(--blue)"/>
    <path d="M370 100c0-10 15-12 15 0 0-12 15-10 15 0 0 10-15 20-15 20s-15-10-15-20z" stroke="var(--red)"/>
    <path d="M44 340c0-10 15-12 15 0 0-12 15-10 15 0 0 10-15 20-15 20s-15-10-15-20z" stroke="var(--purple)"/>
    <path d="M370 330v18h30v-18M385 322v26" stroke="var(--yellow)"/>
  </g>
</svg>

<div class="abs trait t-right" style="left:126px;top:942px">
  <h3><small>Thought </small><span style="color:var(--blue)">Mind</span></h3>
  <p class="small">Sed ut perspiciatis unde omnis iste natus error accusantium doloremque architecto</p>
</div>
<div class="abs trait" style="left:830px;top:942px">
  <h3><span style="color:var(--red)">Heart</span><small> Emotions</small></h3>
  <p class="small">Sed ut perspiciatis unde omnis iste natus error accusantium doloremque architecto</p>
</div>
<div class="abs trait t-right" style="left:126px;top:1170px">
  <h3><small>Intuition </small><span style="color:var(--purple)">Soul</span></h3>
  <p class="small">Sed ut perspiciatis unde omnis iste natus error accusantium doloremque architecto</p>
</div>
<div class="abs trait" style="left:830px;top:1165px">
  <h3><span style="color:var(--gold)">Strength</span><small> Energy</small></h3>
  <p class="small">Sed ut perspiciatis unde omnis iste natus error accusantium doloremque architecto</p>
</div>

<!-- about -->
<section class="about" role="img" aria-label="Faded photo of a laptop on a desk behind the team section"></section>
<h2 class="abs center sec-title" style="top:1425px;font-size:36px">About Us</h2>
<p class="abs center sec-sub" style="top:1488px;font-size:13px">Our team is an unusual mix. We're globally experienced, technically capable, community focussed and highly fruitful.</p>

<div class="person" style="left:140px;top:1555px">
  <div class="portrait" role="img" aria-label="Portrait photo of Marco Dellar" style="background:linear-gradient(160deg,#8aa4c4,#34506e)"></div>
  <h4>Marco Dellar has lived &amp; worked in several countries,<br>experiencing varied cultures &amp; companies.</h4>
  <p class="small">As the Director of Communications at Corvane Inc, Marco leads post-merger integration, culture transformation and leadership development. He blends culture, branding and marketing to enable effective messaging, having lived on several continents and worked in various industries.</p>
  <span class="outline-btn">Learn More</span>
</div>
<div class="person" style="left:637px;top:1555px">
  <div class="portrait" role="img" aria-label="Portrait photo of Ravi Kanter" style="background:linear-gradient(160deg,#b7b7b7,#3c3c3c)"></div>
  <h4>Ravi Kanter is highly experienced as an entrepreneur,<br>business owner and marketing expert.</h4>
  <p class="small">Ravi Kanter, Chief Strategy Officer at Corvane Inc, applies more than two decades of technical sales, partner management and sales team management experience to managing resources for driving profitable growth. Prior to joining Corvane Inc, Ravi held the role of senior account executive.</p>
  <span class="outline-btn">Learn More</span>
</div>

<!-- expand -->
<section class="expand" role="img" aria-label="Colourful background behind the expand section"></section>
<h2 class="abs center expand-title">EXPAND YOUR BUSINESS</h2>
<p class="abs expand-body">BREVLON is powerfully effective because our approach is humanolistic. Our materials are founded upon the idea that Culture is a Person. Marco developed his philosophy on culture over more than three decades, learning from leaders and communities around the globe. We understand at the deepest level that culture is the heartbeat of your company, and as a healthy, strong heart means a healthy, strong person, culture works in a similar fashion. We use the letter X to illustrate this. Similar to how a person is made up of essentially four parts, our programs develop the four pieces of you and your company: thought, emotions, intuition and strengths.</p>
<span class="abs btn expand-btn">Click Here For More Info</span>

<!-- events -->
<h2 class="abs center sec-title" style="top:2610px;font-size:36px">Latest Events</h2>
<p class="abs center sec-sub" style="top:2673px;font-size:13px">Our team is an unusual mix. We're globally experienced, technically capable, community focussed and highly fruitful.</p>

<article class="card" style="left:113px">
  <div class="pic" role="img" aria-label="Photo of business charts and a laptop on a desk" style="background:linear-gradient(135deg,#5d7ea3,#c7d3df)"></div>
  <h5>Education &amp; Networking Events</h5>
  <div class="date">▣ JAN 20, 2019</div>
  <p class="small">We understand at the deepest level that culture is the heartbeat of your company, and as a healthy, heart means a healthy, strong person</p>
</article>
<article class="card" style="left:444px">
  <div class="pic" role="img" aria-label="Photo of a team joining hands over a table" style="background:linear-gradient(135deg,#6f5a45,#c9b49a)"></div>
  <h5>Create Unique,Healthy Culture</h5>
  <div class="date">▣ JAN 20, 2019</div>
  <p class="small">We understand at the deepest level that culture is the heartbeat of your company, and as a healthy, heart means a healthy, strong person</p>
</article>
<article class="card" style="left:776px">
  <div class="pic" role="img" aria-label="Photo of colleagues with tablets around a meeting table" style="background:linear-gradient(135deg,#8c7a66,#e0d6c8)"></div>
  <h5>Education &amp; Networking Events</h5>
  <div class="date">▣ JAN 20, 2019</div>
  <p class="small">We understand at the deepest level that culture is the heartbeat of your company, and as a healthy, heart means a healthy, strong person</p>
</article>

<!-- footer -->
<svg class="abs" style="left:0;top:3210px" width="1200" height="556" viewBox="0 0 1200 556">
  <polygon points="0,118 600,10 1200,118 1200,556 0,556" fill="var(--red)"/>
  <polygon points="0,132 600,24 1200,132 1200,556 0,556" fill="var(--dark)"/>
  <line x1="110" y1="217" x2="1090" y2="217" stroke="var(--line)"/>
  <line x1="110" y1="467" x2="1090" y2="467" stroke="var(--line)"/>
</svg>
<div class="brand abs center" style="top:3312px;font-size:40px;letter-spacing:8px">BREVLON</div>

<div class="foot-col" style="left:109px">
  <div class="foot-icon"><svg width="24" height="24" viewBox="0 0 24 24"><path d="M12 2a7 7 0 0 0-7 7c0 5 7 13 7 13s7-8 7-13a7 7 0 0 0-7-7zm0 9.5A2.5 2.5 0 1 1 12 6.5a2.5 2.5 0 0 1 0 5z" fill="#fff"/></svg></div>
  <h6>Location</h6>
  <p># 254 Harlow Lane, Suite 8, Riverton<br>Westgate District</p>
</div>
<div class="foot-col" style="left:440px">
  <div class="foot-icon"><svg width="22" height="22" viewBox="0 0 24 24"><path d="M6.6 10.8a15 15 0 0 0 6.6 6.6l2.2-2.2a1 1 0 0 1 1-.25 11.4 11.4 0 0 0 3.6.57 1 1 0 0 1 1 1V20a1 1 0 0 1-1 1A17 17 0 0 1 3 4a1 1 0 0 1 1-1h3.5a1 1 0 0 1 1 1c0 1.25.2 2.45.57 3.57a1 1 0 0 1-.25 1z" fill="#fff"/></svg></div>
  <h6>Contact</h6>
  <p>Office: 1-855-555-0142<br>Fax: 000-555-0190</p>
</div>
<div class="foot-col" style="left:769px">
  <div class="foot-icon"><svg width="22" height="22" viewBox="0 0 24 24"><path d="M3 5h18v14H3z" fill="#fff"/><path d="M3 5l9 8 9-8" fill="none" stroke="#111" stroke-width="1.6"/></svg></div>
  <h6>Email</h6>
  <p>connect@brevlon.example<br>www.brevlon.example</p>
</div>
<p class="abs center copy">© Copyright 2019 Brevlon. All rights reserved.</p>

</body>
</html>
```